Breakfast Cafe - The Sunny Nook

It is for my breakfast and lunch cafe with a hawaiian / beach theme. I am open 7 days a week from 7am to 2pm. We serve traditional American food such as omelettes, pancakes, burgers and sandwiches. I'll upload my old card and my new logo to be used. We have a lot of day to day regulars who eat there during the week, our t-shirts actually say 'Locals Only' on them. Hope this helps. Thanks.

Target Market(s)

anyone who has an appetite!

Industry/Entity Type

American Restaurant

Contact Information for Business Card

4815C Marlow Grove Avenue
Long Beach, California
(555) 731-2294

Requirements
Must have
• Address and phone number easily readable.
Nice to have
• beach or tropical theme

```html
<!DOCTYPE html>
<html lang="en">
<head>
<meta charset="utf-8">
<title>The Sunny Nook – Business Card</title>
<link rel="stylesheet" href="https://fonts.googleapis.com/css2?family=Bebas+Neue&display=swap">
<style>
  :root {
    --page-bg: #e9e4dc;
    --card-cream: #efe7d6;
    --card-cream-dark: #e2d7c1;
    --card-night: #1c1d1f;
    --accent-orange: #f0a030;
    --wave-orange: #c8741a;
    --accent-blue: #5bc3dc;
    --ink: #111111;
    --emblem-sun: #f6a93c;
    --emblem-wood: #8a5424;
  }
  * { box-sizing: border-box; margin: 0; padding: 0; }
  html, body {
    width: 1200px;
    height: 960px;
    overflow: hidden;
    background: var(--page-bg);
    font-family: "Bebas Neue", "Arial Narrow", sans-serif;
  }
  .business-card {
    position: absolute;
    left: 300px;
    top: 310px;
    width: 600px;
    height: 342px;
    border-radius: 18px;
    overflow: hidden;
    background: radial-gradient(ellipse at 40% 30%, var(--card-cream) 0%, var(--card-cream-dark) 100%);
    box-shadow: 0 4px 10px rgba(0, 0, 0, 0.18);
  }
  .card-wave {
    position: absolute;
    inset: 0;
    width: 600px;
    height: 342px;
  }
  .emblem-area {
    position: absolute;
    left: 58px;
    top: 42px;
    width: 220px;
    height: 210px;
    border-radius: 50%;
    background: radial-gradient(circle at 50% 40%, var(--emblem-sun) 0%, #e99a3a 45%, var(--emblem-wood) 100%);
  }
  .brand-name {
    position: absolute;
    left: 20px;
    top: 228px;
    width: 296px;
    text-align: center;
    font-size: 50px;
    line-height: 1;
    letter-spacing: 1px;
    color: var(--accent-blue);
  }
  .contact-block {
    position: absolute;
    left: 322px;
    top: 66px;
    color: var(--ink);
  }
  .contact-address {
    font-size: 22px;
    line-height: 22px;
    letter-spacing: 0.3px;
  }
  .contact-phone {
    margin-top: 6px;
    font-size: 29px;
    line-height: 29px;
    letter-spacing: 0.5px;
  }
  .service-block {
    position: absolute;
    left: 322px;
    top: 242px;
  }
  .service-title {
    font-size: 23px;
    line-height: 24px;
    letter-spacing: 0.4px;
    color: var(--accent-orange);
  }
  .service-hours {
    margin-top: 2px;
    font-size: 15px;
    line-height: 16px;
    letter-spacing: 0.4px;
    color: var(--accent-blue);
  }
</style>
</head>
<body>
  <article class="business-card">
    <svg class="card-wave" viewBox="0 0 600 342" aria-hidden="true">
      <path fill="var(--wave-orange)" d="M0 142 C90 119 200 154 300 182 C400 207 520 196 600 108 L600 342 L0 342 Z"/>
      <path fill="var(--card-night)" d="M0 148 C90 125 200 160 300 190 C400 217 522 208 600 126 L600 342 L0 342 Z"/>
    </svg>

    <div class="emblem-area" role="img" aria-label="Round beach-themed cafe emblem illustration with sunset, palm tree and ocean"></div>
    <div class="brand-name">The Sunny Nook</div>

    <div class="contact-block">
      <p class="contact-address">4815C Marlow Grove Avenue<br>Long Beach, California</p>
      <p class="contact-phone">P.(555) 731-2294</p>
    </div>

    <div class="service-block">
      <p class="service-title">Breakfast &amp; Lunch Cafe</p>
      <p class="service-hours">Open 7 days a week from 7am to 2pm.</p>
    </div>
  </article>
</body>
</html>
```